BrivoTerna. Lantern of the Steady Harvest. Business card

Professional business card for BrivoTerna (Lantern of the Steady Harvest)
My rationale: Strategy-> Execution-> Results-> Value that lead to the BrivoTerna name: We put the Lantern of the Steady Harvest.
We deliver value to our customers helping them at defining a good strategy (cyan arrow). 90% of well formulated strategies fail due to poor execution so we also consider strategical execution very important (green arrow). Due to the execution we obtain the results (blue arrow). Finally, the results provide feedback to redefine strategy, and the new strategy has to be executed and new results obtained providing new feedback and on and on. It's like a wheel that finally, must create corporate value: value for shareholders, staholders, employees, providers...-

Target Market(s)

CEOs and steering comitees , invewrnent funds

Industry/Entity Type

Business Consultant

Contact Information for Business Card

Teodoro Vinsquel
CEO & Founder
teodoro.vinsquel@brivoterna-example.com
Mobile: +34 655.803.912
www.brivoterna-example.com

Colors

Designer to choose colors to be used in the design.

Requirements
Nice to have
• Nice to hace the words: Strategy, execution, results
• Nice to vave the claim: Lantern of the Steady Harvest
• The three colors should be shown:
• cyan for STRATEGY
• green for EXECUTION
• blue for RESULTS
Should not have
• Complete black background

```html
<!DOCTYPE html>
<html lang="en">
<head>
<meta charset="utf-8">
<title>BrivoTerna – Business Card</title>
<link rel="stylesheet" href="https://fonts.googleapis.com/css2?family=Roboto:wght@400;500;700&display=swap">
<style>
  :root {
    --backdrop: #a9a9a9;
    --brand-blue: #003296;
    --brand-green: #9bcb3b;
    --brand-cyan: #00aeef;
    --paper: #ffffff;
    --ink-blue: #1a3a8f;
  }
  * { margin: 0; padding: 0; box-sizing: border-box; }
  html, body {
    width: 1200px;
    height: 954px;
    overflow: hidden;
    background: var(--backdrop);
    font-family: "Roboto", Arial, sans-serif;
  }
  .sheet {
    position: relative;
    width: 1200px;
    height: 954px;
  }
  .card {
    position: absolute;
    top: 342px;
    width: 524px;
    height: 300px;
    overflow: hidden;
  }
  .card--front {
    left: 67px;
    background: var(--brand-blue);
  }
  .card--back {
    left: 602px;
    background: var(--paper);
  }
  .wordmark {
    position: absolute;
    font-weight: 700;
    font-size: 40px;
    letter-spacing: -0.5px;
    line-height: 1;
  }
  .card--front .wordmark {
    left: 37px;
    top: 165px;
    color: var(--paper);
  }
  .card--back .wordmark {
    left: 229px;
    top: 68px;
    color: var(--brand-blue);
  }
  .faint-decoration {
    position: absolute;
    left: 376px;
    top: 142px;
    width: 128px;
    height: 155px;
    background: linear-gradient(90deg, rgba(255,255,255,0.22), rgba(255,255,255,0));
  }
  .colour-band-art {
    position: absolute;
    left: 0;
    top: 0;
    width: 152px;
    height: 300px;
    background: linear-gradient(180deg,
      var(--brand-blue) 0%, var(--brand-blue) 52%,
      var(--brand-green) 58%, var(--brand-green) 76%,
      var(--brand-cyan) 82%, var(--brand-cyan) 100%);
  }
  .contact {
    position: absolute;
    left: 230px;
    top: 158px;
    color: var(--ink-blue);
  }
  .contact__name {
    font-size: 17px;
    font-weight: 500;
    color: var(--brand-cyan);
    line-height: 1.1;
  }
  .contact__role {
    font-size: 12px;
    margin-top: 2px;
  }
  .contact__list {
    list-style: none;
    margin-top: 14px;
    font-size: 12.5px;
  }
  .contact__list li {
    display: flex;
    align-items: center;
    gap: 5px;
    height: 20px;
  }
  .contact__icon {
    width: 10px;
    height: 10px;
    flex: none;
  }
</style>
</head>
<body>
  <main class="sheet">
    <section class="card card--front" aria-label="Card front">
      <div class="wordmark">BrivoTerna</div>
      <div class="faint-decoration" role="img" aria-label="Faint decorative brand graphic"></div>
    </section>

    <section class="card card--back" aria-label="Card back">
      <div class="colour-band-art" role="img" aria-label="Large brand graphic in blue, green and cyan for results, execution and strategy"></div>
      <div class="wordmark">BrivoTerna</div>
      <div class="contact">
        <p class="contact__name">Teodoro Vinsquel</p>
        <p class="contact__role">CEO &amp; Founder</p>
        <ul class="contact__list">
          <li>
            <svg class="contact__icon" viewBox="0 0 10 10" aria-hidden="true">
              <path fill="#003296" d="M2.2 0.6l1.6 1.9-0.9 1.2c0.6 1.3 1.6 2.3 2.9 2.9l1.2-0.9 1.9 1.6-0.9 1.9C4.4 9 0.9 5.6 0.4 1.5z"/>
            </svg>
            +34 655.803.912
          </li>
          <li>
            <svg class="contact__icon" viewBox="0 0 10 10" aria-hidden="true">
              <circle cx="5" cy="5" r="4.5" fill="#003296"/>
              <path d="M0.8 5h8.4M5 0.6c-2 2.6-2 6.2 0 8.8M5 0.6c2 2.6 2 6.2 0 8.8" stroke="#fff" stroke-width="0.8" fill="none"/>
            </svg>
            www.brivoterna-example.com
          </li>
          <li>
            <svg class="contact__icon" viewBox="0 0 10 10" aria-hidden="true">
              <rect x="0.5" y="2" width="9" height="6.4" fill="#003296"/>
              <path d="M0.8 2.3L5 5.6l4.2-3.3" stroke="#fff" stroke-width="0.8" fill="none"/>
            </svg>
            teodoro.vinsquel@brivoterna-example.com
          </li>
        </ul>
      </div>
    </section>
  </main>
</body>
</html>
```